Commercial Rooftop Solar business needs a website

We need a website with fantastic appeal for a new company based in Melbourne called Tallow Ridge Energy. We design and install solar energy systems for commercial applications across Australia. Our market is to focus on small to medium businesses looking for solar solutions, but we will also provide our service for residential customers. We would like a beautiful 'front page' feel to our home page, using photographs of solar PV systems and/or natural imagery. Our logo uses the colours orange and black, which could easily be echoed in photographic imagery of sunset and sunrise, for example. The design should communicate quiet confidence and professionalism to a corporate marketplace.

NEW POINTS FOR BRIEF: This design also needs to be flexible to allow for additional future content, including a Support page with sub pages, FAQ's, and a Blog.

As part of this design project, we will require the coding for the website to be completed by the designer.

We have seen some websites, which we like the look and feel of: these are listed below.

brightvanepower.com.au:

• Beautiful images underlaying brief text selling points.
• Simple ‘front cover’ style home page with elegant drop-down menu, stylish simple font style.
• Home page invites exploration through the menu links, rather than trying to provide all the information up front.
• Company logo and name in the top left hand corner, contact details accessible at top right hand, seems consistent in most sites.

kelpworks.com.au

rumbofield.com:
• Same element as the others is the front-page style home page with beautiful images underlying text.

We have a webpage that we started uploading content to. You can use some of the content there in your designs: www.tallowridgeenergy.com.au

Technical Specifications:
PAGES:

Home

About Us

Solutions - Commercial
- Residential

Products - Solar Panels - Vorla Heron, Vorla TELD, Vorla QB
- Solar Inverters - Kestamo, BrilQuill
- Monitoring systems - Dunmere Metrics
- Batteries - RW

- Datasheets have been provided for reference but if it's too much work, you can use generic text and we will provide content later.

Contact Us

FUTURE PAGES (Please consider in structure, where links could be placed):

Support

FAQ's

Blog.

We could provide some content for the Support page soon, but the Blog and FAQ's are future pages which we don't want highlighted in the design as we don't yet have content.

Phone: 1800 7 BIRCH
Email: sales@tallowridgeenergy.com.au

Currently, I do not have images and text available. Please
use placeholders in the meantime. The final text and images will be uploaded for the winner once a winning design has been selected.

Target Market(s)

Primary focus is on small to medium sized business owners. Those owners will have a house which may be suitable for solar so we want to cater to residential deeper in the website.

Industry/Entity Type

Solar Energy

Coding

Coded - Design and coding required

Number of Pages Required

5+ page

Colors
f78f20
0255a3

Requirements
Must have
• Logo as per attachments.
Nice to have
• Logo can have alternate colours Eg. White on Orange or Black etc. provided colour correct logo is shown somewhere eg. footer or contact page.
• In the active site, I'd like to have:
• Very slowly zooming images - barely perceptible.
• Title text that rolls into place
• Subtle movements
• See https://plumtally.com.au/ for example

```html
<!DOCTYPE html>
<html lang="en">
<head>
<meta charset="utf-8">
<title>Residential | Tallow Ridge Energy</title>
<link href="https://fonts.googleapis.com/css2?family=Michroma&family=Open+Sans:wght@400;600;700&display=swap" rel="stylesheet">
<style>
:root{
  --orange:#ef4a1d;
  --orange-deep:#d8360f;
  --navy:#1b3f78;
  --ink:#222;
  --body:#444;
  --white:#fff;
  --footer:#151515;
  --footer-base:#0b0b0b;
  --rule:#2c2c2c;
  --display:'Michroma',sans-serif;
  --text:'Open Sans',sans-serif;
}
*{margin:0;padding:0;box-sizing:border-box}
html,body{width:805px;height:1200px;overflow:hidden;background:var(--white);font-family:var(--text);color:var(--body)}
.page{position:relative;width:805px;height:1200px}

/* hero */
.hero{position:absolute;left:0;top:0;width:805px;height:305px;
  background:linear-gradient(180deg,#3a4656 0%,#5b6877 30%,#2d3a5c 48%,#4a4f58 70%,#7a7c80 100%)}
.hero-band{position:absolute;left:0;top:0;width:805px;height:91px;background:rgba(25,35,50,.55)}
.brand{position:absolute;left:109px;top:30px;color:var(--white);font-family:var(--display);font-size:11px;letter-spacing:1px;line-height:1.5;display:flex;align-items:center;gap:8px;white-space:nowrap}
.brand-dot{width:14px;height:14px;border-radius:50%;background:var(--white)}
.phone{position:absolute;left:495px;top:15px;display:flex;align-items:center;gap:7px;color:var(--white);font-weight:700;font-size:11.5px;white-space:nowrap}
.quote-btn{position:absolute;left:602px;top:14px;width:101px;height:20px;border-radius:10px;background:var(--orange);border:1px solid #fff3;color:var(--white);font-size:9.5px;font-weight:600;display:flex;align-items:center;padding-left:10px;white-space:nowrap}
.nav{position:absolute;top:55px;left:289px;display:flex;gap:13px;font-family:var(--display);font-size:7.6px;letter-spacing:1px;color:var(--white);white-space:nowrap}
.nav .active{color:var(--orange)}
.hero-title{position:absolute;top:166px;left:0;width:805px;text-align:center;font-family:var(--display);font-size:16px;font-weight:400;letter-spacing:4px;color:var(--white)}

/* intro */
.section-title{position:absolute;left:0;width:805px;display:flex;justify-content:center;align-items:center;gap:6px;font-family:var(--display);font-weight:400;font-variant:small-caps;letter-spacing:1.5px;color:var(--ink);white-space:nowrap}
.section-title::before,.section-title::after{content:"";display:block;width:51px;height:1px;background:var(--ink)}
.intro-title{top:336px;font-size:18px}
.why-title{top:587px;font-size:16px}
.lead{position:absolute;left:110px;top:401px;color:var(--orange);font-size:11.5px}
.col{position:absolute;top:425px;font-size:8px;line-height:14.6px;color:var(--body);letter-spacing:.15px}
.col-left{left:110px;width:297px}
.col-right{left:432px;width:270px;text-align:justify}

/* why */
.why{position:absolute;left:0;top:557px;width:805px;height:382px;
  background:linear-gradient(135deg,#f4f6f9 0%,#e9edf2 45%,#dfe4ea 100%)}
.feature{position:absolute;font-size:10px;line-height:14px;color:#333}
.feature.left{text-align:right;width:120px}
.feature.right{text-align:left;width:120px}
.cta{position:absolute;left:322px;top:968px;width:161px;height:22px;border-radius:11px;background:var(--orange);color:var(--white);font-family:var(--display);font-size:6px;letter-spacing:.7px;display:flex;align-items:center;padding-left:8px;white-space:nowrap}
.cta-arrow{position:absolute;right:4px;top:4px;width:14px;height:14px;border-radius:50%;background:var(--white)}
.cta-arrow svg{display:block}

/* footer */
.footer{position:absolute;left:0;top:1018px;width:805px;height:154px;background:var(--footer);color:#ddd}
.footer-base{position:absolute;left:0;top:1172px;width:805px;height:28px;background:var(--footer-base);color:#ccc;font-size:7px;text-align:center;line-height:28px}
.f-head{position:absolute;top:22px;font-family:var(--display);font-weight:400;font-variant:small-caps;font-size:8.5px;letter-spacing:.8px;color:var(--white);padding-bottom:6px;border-bottom:1px solid #333;white-space:nowrap}
.f-links{position:absolute;left:111px;top:50px;list-style:none;font-size:7.5px;line-height:17.6px}
.f-links li::before{content:"› ";color:#777}
.f-divider{position:absolute;top:34px;width:1px;height:110px;background:var(--rule)}
.field{position:absolute;left:246px;width:128px;background:var(--white);border-radius:2px;color:#777;font-size:6.5px;padding:2px 4px}
.submit{position:absolute;left:246px;top:128px;width:46px;height:14px;border-radius:7px;background:var(--orange);color:var(--white);font-family:var(--display);font-size:5px;letter-spacing:.5px;text-align:center;line-height:14px}
.contact-row{position:absolute;left:410px;width:140px;font-size:7.3px;display:flex;align-items:center;gap:5px;padding-bottom:6px;border-bottom:1px solid #2a2a2a;white-space:nowrap}
.contact-name{position:absolute;left:410px;top:114px;font-size:8.5px;font-weight:700;color:var(--white);display:flex;gap:6px;white-space:nowrap}
.contact-sub{position:absolute;left:423px;top:131px;font-size:7.5px}
.f-brand{position:absolute;left:590px;top:74px;width:123px;text-align:center;font-family:var(--display);font-size:9px;letter-spacing:1px;color:var(--white);line-height:1.5;white-space:nowrap}
.abn{position:absolute;left:590px;top:126px;width:123px;text-align:center;font-size:7.8px}
</style>
</head>
<body>
<div class="page">

  <header class="hero" role="img" aria-label="Photo of solar panels on a house roof near the coast">
    <div class="hero-band"></div>
  </header>
  <div class="brand"><span class="brand-dot"></span><span>TALLOW RIDGE<br>ENERGY</span></div>
  <div class="phone">
    <svg width="20" height="20" viewBox="0 0 20 20"><circle cx="10" cy="10" r="9" fill="none" stroke="#fff" stroke-width="1.4"/><path d="M7 5.5l1.6 2.4-1 1.1c.6 1.3 1.6 2.3 2.9 2.9l1.1-1 2.4 1.6-.9 1.6c-3.5-.3-6.7-3.5-7-7z" fill="#fff"/></svg>
    1800 7 BIRCH
  </div>
  <div class="quote-btn">FREE QUOTE</div>
  <nav class="nav">
    <span>HOME</span><span>ABOUT US</span><span>COMMERCIAL</span><span class="active">RESIDENTIAL</span><span>PRODUCTS</span><span>CONTACT</span>
  </nav>
  <h1 class="hero-title">GO SOLAR AT HOME</h1>

  <h2 class="section-title intro-title">Residential</h2>
  <p class="lead">Do you want power that protects the planet?</p>
  <p class="col col-left">Powering your home with solar energy does this and more: by installing solar you also protect your household budget from the rising price of electricity from the grid. And there’s even more good news: because of Australian government rebates and State feed-in tariffs, you can often gain financially from investing in your own solar energy system. Tallow Ridge Energy can provide you with an electricity supply that provides a benefit to your budget, whilst empowering you to break free from fossil-fuel energy.</p>
  <p class="col col-right">Tallow Ridge Energy provides quality guaranteed components, professionally installed by Clean Power Guild approved installers. Our award-winning designer will ensure that your solar energy system is the best fit for your energy needs. We provide monitoring and ongoing technical support, to ensure that your system functions optimally and reliably. Contact us for more information and for a quote today.</p>

  <section class="why" role="img" aria-label="Soft photo of solar panel cells against the sky"></section>
  <h2 class="section-title why-title">Why Choose Tallow Ridge Energy</h2>

  <svg style="position:absolute;left:0;top:0" width="805" height="1200" aria-hidden="true">
    <defs>
      <linearGradient id="badge" x1="0" y1="0" x2="1" y2="1"><stop offset="0" stop-color="#f5561f"/><stop offset="1" stop-color="#d8300e"/></linearGradient>
    </defs>
    <circle cx="403" cy="779" r="96" fill="none" stroke="#888" stroke-width=".8"/>
    <g stroke="#333" stroke-width=".8" stroke-dasharray="2 2" fill="none">
      <path d="M287 680h13l35 28"/><path d="M287 779h18"/><path d="M287 876h13l35-28"/>
      <path d="M517 680h-13l-36 28"/><path d="M517 779h-19"/><path d="M517 876h-13l-36-28"/>
    </g>
    <g fill="#143a6b" stroke="#fff" stroke-width="1.5">
      <circle cx="335" cy="708" r="4"/><circle cx="305" cy="779" r="4"/><circle cx="335" cy="848" r="4"/>
      <circle cx="468" cy="708" r="4"/><circle cx="498" cy="779" r="4"/><circle cx="468" cy="848" r="4"/>
    </g>
    <g fill="url(#badge)" stroke="#1b3f78" stroke-width="1.2">
      <circle cx="261" cy="680" r="25"/><circle cx="261" cy="779" r="25"/><circle cx="261" cy="876" r="25"/>
      <circle cx="543" cy="680" r="25"/><circle cx="543" cy="779" r="25"/><circle cx="543" cy="876" r="25"/>
    </g>
    <g fill="none" stroke="#fff" stroke-width="1.6" stroke-linecap="round" stroke-linejoin="round">
      <rect x="248" y="671" width="26" height="16" rx="1.5"/><path d="M256 692h10M252 679h5l2-4 3 7 2-3h6"/>
      <circle cx="261" cy="775" r="8"/><path d="M256 782l-3 8 4-1 2 3 2-6M266 782l3 8-4-1-2 3-2-6"/>
      <circle cx="261" cy="866" r="5"/><path d="M251 882c0-6 4-9 10-9s10 3 10 9z"/>
      <path d="M533 690l14-14M549 670l5 5-4 4-5-5zM537 670l16 18M533 672l4-4"/>
      <circle cx="543" cy="775" r="9"/><path d="M538 776h3v5h-3zM541 776l3-5c1 0 2 1 1 3h4l-1 6h-7"/><path d="M538 783l-3 7 4-1 2 3M548 783l3 7-4-1-2 3"/>
      <circle cx="537" cy="873" r="5"/><path d="M537 863v-3M529 873h-3M531 866l-2-2M545 866l2-2M542 880l6 4v5M546 889h4"/>
    </g>
    <g fill="#fff"><path d="M254 885l1.2 2.4 2.6.3-1.9 1.8.5 2.6-2.4-1.3-2.4 1.3.5-2.6-1.9-1.8 2.6-.3zM261 885l1.2 2.4 2.6.3-1.9 1.8.5 2.6-2.4-1.3-2.4 1.3.5-2.6-1.9-1.8 2.6-.3zM268 885l1.2 2.4 2.6.3-1.9 1.8.5 2.6-2.4-1.3-2.4 1.3.5-2.6-1.9-1.8 2.6-.3z"/></g>
  </svg>

  <div class="feature left" style="left:105px;top:666px">Comprehensive<br>Monitoring</div>
  <div class="feature left" style="left:105px;top:765px">Performance<br>Guaranteed</div>
  <div class="feature left" style="left:105px;top:862px">Top Quality<br>Components</div>
  <div class="feature right" style="left:581px;top:666px">Maintenance<br>Included</div>
  <div class="feature right" style="left:581px;top:766px">Experienced<br>Installers</div>
  <div class="feature right" style="left:581px;top:861px">10 Year System<br>Warranty</div>

  <div class="cta">REQUEST A FREE QUOTE<span class="cta-arrow"><svg width="14" height="14" viewBox="0 0 14 14"><path d="M6 4.5l2.5 2.5L6 9.5" fill="none" stroke="#222" stroke-width="1.4" stroke-linecap="round"/></svg></span></div>

  <footer class="footer">
    <h3 class="f-head" style="left:111px;width:73px">Quick Links</h3>
    <ul class="f-links"><li>Home</li><li>About Us</li><li>Commercial</li><li>Residential</li><li>Products</li><li>Contact Us</li></ul>
    <span class="f-divider" style="left:216px"></span>

    <h3 class="f-head" style="left:246px;width:129px">Quick Inquiry</h3>
    <div class="field" style="top:46px;height:13px">Name</div>
    <div class="field" style="top:63px;height:13px">Email</div>
    <div class="field" style="top:81px;height:42px">Message</div>
    <div class="submit">SUBMIT</div>
    <span class="f-divider" style="left:393px"></span>

    <h3 class="f-head" style="left:410px;width:140px">Contact Details</h3>
    <div class="contact-row" style="top:45px"><svg width="8" height="8" viewBox="0 0 8 8"><path d="M1 0.5l1.6 2-1 1c.6 1.2 1.4 2 2.6 2.6l1-1 2 1.6-1 1.5C3.3 8 .2 4.8 0 1.5z" fill="#ef4a1d"/></svg>1800 7 BIRCH</div>
    <div class="contact-row" style="top:68px"><svg width="8" height="6" viewBox="0 0 8 6"><rect width="8" height="6" fill="#ef4a1d"/><path d="M0 0l4 3 4-3" stroke="#151515" fill="none" stroke-width=".8"/></svg>enquiries@tallowridgeenergy.com.au</div>
    <div class="contact-row" style="top:91px"><svg width="8" height="8" viewBox="0 0 8 8"><circle cx="4" cy="4" r="3.4" fill="none" stroke="#ef4a1d"/><path d="M.6 4h6.8M4 .6c-2 2-2 4.8 0 6.8M4 .6c2 2 2 4.8 0 6.8" stroke="#ef4a1d" fill="none" stroke-width=".6"/></svg>www.tallowridgeenergy.com.au</div>
    <div class="contact-name"><svg width="7" height="10" viewBox="0 0 7 10"><path d="M3.5 0C1.6 0 0 1.5 0 3.4 0 6 3.5 10 3.5 10S7 6 7 3.4C7 1.5 5.4 0 3.5 0z" fill="#ef4a1d"/><circle cx="3.5" cy="3.4" r="1.3" fill="#151515"/></svg>TALLOW RIDGE ENERGY</div>
    <div class="contact-sub">Kestrel Vale, Victoria</div>
    <span class="f-divider" style="left:574px"></span>

    <div class="f-brand">TALLOW RIDGE<br>ENERGY</div>
    <div class="abn">ABN: 41 502 773 160</div>
  </footer>
  <div class="footer-base">Copyright © 2017 Tallow Ridge Energy. All Right Reserved.</div>
</div>
</body>
</html>
```